Meridale Bed Company Needs Business Card

Looking for a very nice looking business card. Creative but not extravagant. We sell beds and pillows across the U.S. and need something professional but catchy. I have attached the logo.

Name : Devin Holt
Title : President
Phone : (800) 471-2960
Email: sleep@quilmora.com
Website: www.quilmora.com

Can be single-sided or double-sided
horizontal or vertical

Can use Blues/Greys

Target Market(s)

Mass Market

Industry/Entity Type

Retail

Contact Information for Business Card

Name : Devin Holt
Title : President
Phone : (800) 471-2960
Email: sleep@quilmora.com
Website: www.quilmora.com

Requirements
Must have
• Clean, Modern, Smooth
• Can use Blues/Greys
• On the other side without the information - have something simple like www.quilmora.com or our logo
Nice to have
• Surprise me
Should not have
• Nothing crazy, nothing cluttered

```html
<!DOCTYPE html>
<html lang="en">
<head>
<meta charset="utf-8">
<title>Meridale Bed Company – Business Card</title>
<link rel="stylesheet" href="https://fonts.googleapis.com/css2?family=Open+Sans:wght@300;400;600;700&display=swap">
<style>
  :root {
    --brand-blue: #31a4d6;
    --frost-top: #f4f5f6;
    --frost-bottom: #e4e7e9;
    --page-bg: #eceef0;
    --white: #ffffff;
    --card-shadow: rgba(30, 50, 70, 0.18);
  }
  html, body {
    margin: 0;
    padding: 0;
    overflow: hidden;
  }
  body {
    width: 1200px;
    height: 900px;
    background: var(--page-bg);
    position: relative;
    font-family: "Open Sans", Arial, sans-serif;
  }
  .card {
    position: absolute;
    display: flex;
    flex-direction: column;
    box-shadow: 0 6px 18px var(--card-shadow);
    overflow: hidden;
  }
  .card--front { left: 238px; top: 62px; width: 555px; height: 343px; }
  .card--back  { left: 459px; top: 518px; width: 560px; height: 344px; }

  .card__frost {
    background: linear-gradient(180deg, var(--frost-top), var(--frost-bottom));
    position: relative;
  }
  .card--front .card__frost { height: 185px; }
  .card--back .card__frost  { height: 187px; }

  .card__band {
    flex: 1;
    background: var(--brand-blue);
    color: var(--white);
    position: relative;
  }

  .wordmark {
    position: absolute;
    margin: 0;
    font-weight: 300;
    color: var(--brand-blue);
    letter-spacing: 2px;
    line-height: 1;
  }
  .card--front .wordmark { left: 112px; top: 52px; font-size: 90px; }
  .wordmark--faint {
    left: 112px; top: 62px; font-size: 82px;
    opacity: 0.3;
    transform: scaleX(-1);
  }

  .holder {
    position: absolute;
    right: 324px;
    top: 46px;
    text-align: right;
  }
  .holder__name { margin: 0; font-size: 18px; font-weight: 700; line-height: 22px; }
  .holder__title { margin: 0; font-size: 15px; font-weight: 400; line-height: 20px; }

  .contacts {
    position: absolute;
    left: 270px;
    top: 40px;
    margin: 0;
    padding: 0;
    list-style: none;
    font-size: 15px;
    line-height: 20px;
  }
  .contacts li { display: flex; align-items: center; gap: 8px; }
  .contacts svg { width: 12px; height: 12px; fill: var(--white); flex: none; }

  .back-url {
    position: absolute;
    left: 0; right: 0;
    bottom: 32px;
    text-align: center;
    font-size: 15px;
  }
</style>
</head>
<body>

  <section class="card card--front" aria-label="Business card front">
    <div class="card__frost">
      <p class="wordmark">quilmora</p>
    </div>
    <div class="card__band">
      <div class="holder">
        <p class="holder__name">Devin Holt</p>
        <p class="holder__title">President</p>
      </div>
      <ul class="contacts">
        <li>
          <svg viewBox="0 0 12 12" aria-hidden="true"><path d="M2.4 0.6l1.9 2.1-1 1.2c.7 1.6 1.9 2.9 3.6 3.7l1.2-1 2.2 1.8-.9 2.2C5.2 10.6 1.2 6.7.3 1.5z"/></svg>
          (800) 471-2960
        </li>
        <li>
          <svg viewBox="0 0 12 12" aria-hidden="true"><path d="M1 3h10v6.5H1z M1 3l5 3.6L11 3" stroke="#31a4d6" stroke-width="0.9"/></svg>
          sleep@quilmora.com
        </li>
        <li>
          <svg viewBox="0 0 12 12" aria-hidden="true"><circle cx="6" cy="6" r="5.5"/><path d="M3 4.5c1 .3 1.5 1 1.2 2 .8.4 1 1.2.6 2.3M7.5 2c-.3 1 .2 1.6 1.2 1.8.4 1 .1 2-.8 2.4" stroke="#31a4d6" stroke-width="0.9" fill="none"/></svg>
          www.quilmora.com
        </li>
      </ul>
    </div>
  </section>

  <section class="card card--back" aria-label="Business card back">
    <div class="card__frost">
      <p class="wordmark wordmark--faint" aria-hidden="true">quilmora</p>
    </div>
    <div class="card__band">
      <p class="back-url">www.quilmora.com</p>
    </div>
  </section>

</body>
</html>
```